Custom Cabinet Shop Needs a website design

Hi,
We need a website for a Custom Cabinet Shop and Cabinet parts manufacturing business.
The business has two sides to it. One side provides custom Kitchens, vanities, entertainment units, offices and what not to homeowners and contractors.
The 2nd side of the business provides built to order cabinet boxes and other parts required to put together a project to other cabinet shops, small contractors looking to install there own cabinets.
Website will need a Gallery to display work.
Color scheme to go well with logo.
current website is www.brambleoakcustomcabinets.com
being changed to www.brambleoak.ca
Logo Included in attached files.
Tagline "Joinery with Spirit"
Mission Statement "Our passion is to deliver inspired cabinetry solutions to suit all your needs, supported by our phenomenal star class customer service"
The website should convey quality and professionalism.
Thank you.
Homeowners/ Contractors
Entertainment

```html
<!DOCTYPE html>
<html lang="en">
<head>
<meta charset="utf-8">
<title>Bramble Oak Custom Cabinets</title>
<link href="https://fonts.googleapis.com/css2?family=Open+Sans:ital,wght@0,300;0,400;0,600;0,700;1,400&display=swap" rel="stylesheet">
<style>
:root{
  --orange:#e2471c;
  --ink:#333333;
  --muted:#6b6b6b;
  --soft:#ececec;
  --line:#d4d4d4;
  --footer:#2a2a2a;
  --white:#ffffff;
}
*{margin:0;padding:0;box-sizing:border-box}
html,body{width:870px;height:1200px;overflow:hidden;background:var(--white)}
body{font-family:"Open Sans",Arial,sans-serif;color:var(--ink);position:relative}
.abs{position:absolute}

/* header */
.site-header{position:absolute;left:0;top:0;width:870px;height:85px;background:var(--white)}
.brand{position:absolute;left:72px;top:28px;display:flex;align-items:center;gap:8px}
.brand-mark{width:22px;height:22px;background:var(--orange)}
.brand-name{font-weight:700;font-size:17px;color:var(--ink);letter-spacing:.5px}
.login{position:absolute;left:739px;top:32px;width:60px;height:25px;background:#333;color:#fff;border-radius:3px;font-size:10px;text-align:center;line-height:25px}

/* nav */
.main-nav{position:absolute;left:0;top:85px;width:870px;height:32px;background:var(--orange)}
.main-nav span{position:absolute;top:0;line-height:32px;color:#fff;font-size:9.5px;transform:translateX(-50%)}
.main-nav i{position:absolute;top:0;width:1px;height:32px;background:rgba(0,0,0,.12)}

/* hero */
.hero{position:absolute;left:0;top:117px;width:870px;height:335px;background:linear-gradient(90deg,#3a3230 0%,#5a4f49 30%,#2b2828 55%,#6b625c 80%,#8d8883 100%)}
.hero h1{position:absolute;left:0;width:870px;top:151px;text-align:center;color:#fff;font-weight:300;font-size:30px;letter-spacing:.5px}
.dots{position:absolute;left:430px;top:304px;display:flex;gap:4px}
.dots b{width:8px;height:8px;border-radius:50%;background:#ccc}
.dots b.on{background:var(--orange)}

/* section headings */
.section-title{position:absolute;left:0;width:870px;text-align:center;color:var(--orange);font-size:13.5px;font-weight:600}
.rule{position:absolute;height:2px;border-top:1px solid var(--line);border-bottom:1px solid #f3f3f3}
.intro{position:absolute;left:100px;width:670px;text-align:center;color:var(--muted);font-size:9.5px;line-height:18px}

/* features */
.feature{position:absolute;top:570px;width:220px}
.feature .icon{position:absolute;left:0;top:0;width:36px;height:36px;border-radius:50%;background:#bdbdbd}
.feature .icon.active{background:var(--orange)}
.feature h3{position:absolute;left:51px;top:3px;font-weight:400;font-size:11.5px;color:#222;white-space:nowrap}
.feature p{position:absolute;left:51px;top:24px;width:170px;font-family:Arial,sans-serif;font-size:7.5px;line-height:14.5px;color:#777}

/* gallery */
.gallery{position:absolute;left:0;top:661px;width:870px;height:292px;background:var(--soft)}
.thumb{position:absolute;top:137px;width:164px;height:117px;border:2px solid #fff}
.thumb-shadow{position:absolute;top:256px;width:164px;height:8px;background:radial-gradient(ellipse at 50% 0,rgba(0,0,0,.18),rgba(0,0,0,0) 70%)}

/* testimonials */
.testimonials-title{position:absolute;left:72px;top:974px;color:var(--orange);font-size:13.5px;font-weight:600}
.testimonial{position:absolute;width:230px}
.testimonial .q{position:absolute;left:0;top:0;font-size:20px;color:#aaa;font-family:Georgia,serif;font-weight:700;line-height:1}
.testimonial .photo{position:absolute;left:18px;top:3px;width:50px;height:46px;border:2px solid #fff;box-shadow:0 0 2px #bbb;background:linear-gradient(160deg,#c9d6e3,#8a9aab)}
.testimonial .lead{position:absolute;left:78px;top:5px;width:155px;font-style:italic;font-size:7.3px;line-height:12.5px;color:#555}
.testimonial .body{position:absolute;left:17px;top:56px;width:220px;font-style:italic;font-size:7.3px;line-height:12.5px;color:#555}
.testimonial .close{position:absolute;left:153px;top:92px;font-size:12px;color:#aaa;font-family:Georgia,serif;font-weight:700}
.testimonial .author{position:absolute;left:17px;top:102px;font-size:7.8px;font-weight:600;color:#333}

/* footer */
.site-footer{position:absolute;left:0;top:1131px;width:870px;height:69px;background:var(--footer)}
.footer-links{position:absolute;left:72px;top:18px;font-size:7.8px;color:#fff;word-spacing:2px}
.footer-links em{font-style:normal;margin:0 16px}
.copyright{position:absolute;left:72px;top:41px;font-size:7.8px;color:#ddd}
.social{position:absolute;left:694px;top:24px;display:flex;gap:8px}
.social b{width:20px;height:20px;border-radius:50%;border:2px solid #fff;background:transparent}
</style>
</head>
<body>

<header class="site-header">
  <div class="brand"><span class="brand-mark"></span><span class="brand-name">BRAMBLE OAK</span></div>
  <div class="login">LOGIN</div>
</header>

<nav class="main-nav">
  <span style="left:87px">HOME</span>
  <i style="left:170px"></i>
  <span style="left:247px">GALLERY</span>
  <i style="left:332px"></i>
  <span style="left:411px">SERVICES</span>
  <i style="left:502px"></i>
  <span style="left:585px">WARRANTY</span>
  <i style="left:686px"></i>
  <span style="left:775px">CONTACT</span>
</nav>

<section class="hero" role="img" aria-label="Photo of a bedroom with dark built-in cabinetry around a fireplace">
  <h1>JOINERY WITH SPIRIT</h1>
  <div class="dots"><b></b><b class="on"></b><b></b></div>
</section>

<h2 class="section-title" style="top:472px">WELCOME TO OUR COMPANY</h2>
<div class="rule" style="left:143px;top:504px;width:265px"></div>
<div class="rule" style="left:463px;top:504px;width:265px"></div>
<p class="intro" style="top:525px">Our passion is to deliver inspired cabinetry solutions to suit all your needs, supported by our phenomenal star class customer service</p>

<div class="feature" style="left:73px">
  <div class="icon active"><svg width="36" height="36" viewBox="0 0 36 36"><circle cx="18" cy="18" r="5" fill="none" stroke="#fff" stroke-width="3"/><circle cx="18" cy="18" r="7.5" fill="none" stroke="#fff" stroke-width="2" stroke-dasharray="3 2.9"/></svg></div>
  <h3>Lorem Ipsum is a dummy</h3>
  <p>Lorem Ipsum is simply dummy text of the printing and typesetting industry. Lorem Ipsum has been the industry's...</p>
</div>
<div class="feature" style="left:324px">
  <div class="icon"><svg width="36" height="36" viewBox="0 0 36 36"><path d="M11 24c2-9 8-12 15-12-1 8-5 13-13 12" fill="none" stroke="#fff" stroke-width="2"/></svg></div>
  <h3>Lorem Ipsum is a dummy</h3>
  <p>Lorem Ipsum is simply dummy text of the printing and typesetting industry. Lorem Ipsum has been the industry's...</p>
</div>
<div class="feature" style="left:584px">
  <div class="icon"><svg width="36" height="36" viewBox="0 0 36 36"><ellipse cx="15" cy="16" rx="6" ry="5" fill="#fff"/><ellipse cx="21" cy="20" rx="6" ry="5" fill="#fff" stroke="#bdbdbd" stroke-width="1"/></svg></div>
  <h3>Lorem Ipsum is a dummy</h3>
  <p>Lorem Ipsum is simply dummy text of the printing and typesetting industry. Lorem Ipsum has been the industry's...</p>
</div>

<section class="gallery">
  <h2 class="section-title" style="top:15px">GALLERY</h2>
  <div class="rule" style="left:143px;top:49px;width:265px"></div>
  <div class="rule" style="left:463px;top:49px;width:265px"></div>
  <p class="intro" style="top:71px;left:110px;width:650px">At vero eos et accusamus et iusto odio dignissimos ducimus qui blanditiis praesentium voluptatum deleniti atque corrupti quos dolores et quas molestias excepturi sint occaecati cupiditate</p>
  <div class="thumb" style="left:71px;background:linear-gradient(135deg,#4a3a32,#2a211d 60%,#7a5a40)" role="img" aria-label="Kitchen island with dark cabinetry and bar stools"></div>
  <div class="thumb-shadow" style="left:71px"></div>
  <div class="thumb" style="left:260px;background:linear-gradient(135deg,#1d2430,#3b2a24 55%,#1f3a5a)" role="img" aria-label="Tall glass-front display cabinet with drawers"></div>
  <div class="thumb-shadow" style="left:260px"></div>
  <div class="thumb" style="left:447px;background:linear-gradient(180deg,#3a3434,#2a2423 50%,#6a2f22)" role="img" aria-label="Entertainment unit below a wall-mounted television"></div>
  <div class="thumb-shadow" style="left:447px"></div>
  <div class="thumb" style="left:634px;background:linear-gradient(135deg,#6a5a4a,#3a1f1a 55%,#2a1614)" role="img" aria-label="Wet bar with wine rack and dark wood cabinets"></div>
  <div class="thumb-shadow" style="left:634px"></div>
</section>

<h2 class="testimonials-title">CUSTOMER TESTIMONIALS</h2>

<div class="testimonial" style="left:72px;top:1010px">
  <span class="q">&ldquo;</span>
  <div class="photo" role="img" aria-label="Portrait of a customer"></div>
  <p class="lead">Northgate Mentoring works with executives at under-performing organizations experiencing a range of issues</p>
  <p class="body">Northgate Mentoring works witha range of issues from mild dys-function to significant distress. We help them pivot, and achieve renewed growth.</p>
  <span class="close">&rdquo;</span>
  <span class="author">By Author Name</span>
</div>
<div class="testimonial" style="left:318px;top:1004px">
  <span class="q">&ldquo;</span>
  <div class="photo" role="img" aria-label="Portrait of a customer"></div>
  <p class="lead">Northgate Mentoring works with executives at under-performing organizations experiencing a range of issues</p>
  <p class="body">Northgate Mentoring works witha range of issues from mild dys-function to significant distress. We help them pivot, and achieve renewed growth.</p>
  <span class="close">&rdquo;</span>
  <span class="author">By Author Name</span>
</div>
<div class="testimonial" style="left:574px;top:1006px">
  <span class="q">&ldquo;</span>
  <div class="photo" role="img" aria-label="Portrait of a customer"></div>
  <p class="lead">Northgate Mentoring works with executives at under-performing organizations experiencing a range of issues</p>
  <p class="body">Northgate Mentoring works witha range of issues from mild dys-function to significant distress. We help them pivot, and achieve renewed growth.</p>
  <span class="close">&rdquo;</span>
  <span class="author">By Author Name</span>
</div>

<footer class="site-footer">
  <div class="footer-links">HOME<em>/</em>GALLERY<em>/</em>SERVICES<em>/</em>WARRANTY<em>/</em>CONTACT</div>
  <div class="copyright">Copyright &copy; 2015. Bramble Oak. All Rights Reserved.</div>
  <div class="social" aria-label="Social links"><b></b><b></b><b></b><b></b></div>
</footer>

</body>
</html>
```